Calvanto Group Real Estate Company business cards

New business card design, we are generally happy with the basic layout of the existing front of business card, (feel free to change) but require a head shot photo on the back side.

http://www.calvanto.com.au/

Attached logos, and existing business card

------------------------------

Target Market(s)

Real estate

Industry/Entity Type

Real Estate

Contact Information for Business Card

Standard size double sided

Font styles to use
Other font styles liked:
• Futura

Requirements
Must have
• Photo head shot on the back side
Nice to have
• yes
Should not have
• No

```html
<!DOCTYPE html>
<html lang="en">
<head>
<meta charset="utf-8">
<title>Calvanto Group – Business Cards</title>
<link rel="stylesheet" href="https://fonts.googleapis.com/css2?family=Jost:ital,wght@0,400;0,500;0,600;1,700&display=swap">
<style>
  :root {
    --bg: #e4e4e4;
    --card: #fbfbfb;
    --navy: #2a2358;
    --purple: #4a2a7c;
    --orange: #f08a1c;
    --ink: #2f2f3a;
    --muted: #8a8a96;
  }
  * { box-sizing: border-box; margin: 0; padding: 0; }
  html, body { width: 1200px; height: 1200px; overflow: hidden; }
  body {
    background: var(--bg);
    font-family: "Jost", "Futura", sans-serif;
    position: relative;
  }
  .card {
    position: absolute;
    left: 170px;
    width: 860px;
    height: 491px;
    background: var(--card);
    border-radius: 26px;
    overflow: hidden;
    box-shadow: 0 6px 18px rgba(0,0,0,.18);
  }
  .card--front { top: 80px; }
  .card--back { top: 629px; }

  /* front */
  .tagline {
    position: absolute; left: 64px; top: 140px;
    font-size: 46px; line-height: 1.04; color: var(--navy); font-weight: 400;
  }
  .tagline .accent { color: var(--orange); display: block; }
  .brand {
    position: absolute;
    font-weight: 500; color: var(--navy); letter-spacing: -1px;
    display: flex; align-items: center; gap: 14px;
    white-space: nowrap;
  }
  .brand__mark {
    width: 18px; height: 18px; background: var(--orange); display: inline-block;
  }
  .card--front .brand { left: 64px; top: 370px; font-size: 58px; }
  .headshot {
    position: absolute; right: 0; top: 0; width: 380px; height: 350px;
    background: radial-gradient(ellipse at 55% 95%, #2d3a5e 0%, #3e4c72 30%, #b9bfcd 55%, #f3f3f3 75%);
  }

  /* back */
  .back-art { position: absolute; inset: 0; }
  .person {
    position: absolute; right: 74px; top: 42px; text-align: right; color: #fff;
  }
  .person__name { font-size: 30px; font-weight: 700; font-style: italic; }
  .person__role { font-size: 18px; font-weight: 400; margin-top: 2px; }
  .contacts {
    position: absolute; left: 120px; top: 286px; list-style: none;
    font-size: 22px; color: var(--ink); line-height: 36px;
  }
  .contacts li { display: flex; align-items: center; gap: 16px; }
  .contacts svg { width: 20px; height: 20px; flex: none; }
  .card--back .brand { left: 110px; top: 392px; font-size: 64px; }
  .company-info {
    position: absolute; right: 64px; top: 280px; text-align: right;
    font-size: 19px; color: var(--ink); line-height: 32px;
  }
  .social { display: inline-flex; gap: 6px; vertical-align: middle; margin-left: 8px; }
  .social span { width: 22px; height: 22px; border-radius: 4px; background: var(--orange); display: inline-block; }
</style>
</head>
<body>

<section class="card card--front" aria-label="Business card front">
  <div class="headshot" role="img" aria-label="Head shot photo of the director in a navy suit and blue tie"></div>
  <p class="tagline">Let us<br>show you<span class="accent">property</span></p>
  <div class="brand"><span class="brand__mark"></span>Calvanto Group</div>
</section>

<section class="card card--back" aria-label="Business card back">
  <svg class="back-art" viewBox="0 0 860 491" preserveAspectRatio="none" aria-hidden="true">
    <path d="M0 0 H860 V128 C700 120 560 150 420 180 C260 214 110 222 0 262 Z" fill="var(--purple)"/>
    <path d="M0 262 C110 222 260 214 420 180 C560 150 700 120 860 128 V144 C700 138 560 168 420 198 C270 230 120 246 0 290 Z" fill="#fbfbfb"/>
    <path d="M0 284 C120 240 270 226 420 194 C560 164 700 134 860 140 V152 C700 148 560 178 420 208 C270 240 120 258 0 304 Z" fill="var(--orange)"/>
    <path d="M60 268 C180 232 320 214 460 186 C380 206 240 226 60 274 Z" fill="var(--orange)"/>
  </svg>

  <div class="person">
    <div class="person__name">Daniel Tran</div>
    <div class="person__role">Director</div>
  </div>

  <ul class="contacts">
    <li><svg viewBox="0 0 20 20"><rect x="5" y="1" width="10" height="18" rx="2" fill="var(--orange)"/><rect x="7" y="4" width="6" height="10" fill="#fff"/></svg>0400 555 018</li>
    <li><svg viewBox="0 0 20 20"><circle cx="10" cy="10" r="9" fill="var(--orange)"/><path d="M1 10h18M10 1c-4 5-4 13 0 18M10 1c4 5 4 13 0 18" stroke="#fff" stroke-width="1.4" fill="none"/></svg>www.calvanto.com.au</li>
    <li><svg viewBox="0 0 20 20"><rect x="1" y="4" width="18" height="12" rx="1" fill="var(--orange)"/><path d="M1 5l9 6 9-6" stroke="#fff" stroke-width="1.6" fill="none"/></svg>daniel.tran@calvanto.com.au</li>
  </ul>

  <div class="company-info">
    <div>Find us: <span class="social"><span></span><span></span><span></span></span></div>
    <div>ABN: 12 345 678 901</div>
  </div>

  <div class="brand"><span class="brand__mark"></span>Calvanto Group</div>
</section>

</body>
</html>
```